Copper Ridge Inquiries Letterhead

I would like to design a letterhead for a private investigation company. Our primary clients will be law firms. The business card is included below

```html
<!DOCTYPE html>
<html lang="en">
<head>
<meta charset="utf-8">
<title>Copper Ridge Inquiries Letterhead</title>
<link rel="stylesheet" href="https://fonts.googleapis.com/css2?family=Montserrat:wght@400;700&family=Lato:wght@400;700&family=Italianno&display=swap">
<style>
  :root {
    --navy: #14214f;
    --orange: #d8461f;
    --paper: #efefef;
    --backdrop: #dedede;
    --ink: #111111;
  }
  * { margin: 0; padding: 0; box-sizing: border-box; }
  html, body { width: 1200px; height: 1141px; overflow: hidden; background: var(--backdrop); }
  .letterhead {
    position: absolute; left: 225px; top: 40px;
    width: 750px; height: 1060px;
    background: var(--paper);
    box-shadow: 0 2px 10px rgba(0,0,0,0.18);
    overflow: hidden;
    font-family: "Lato", sans-serif; color: var(--ink);
  }
  .brand { position: absolute; left: 24px; top: 58px; width: 200px; text-align: center; }
  .brand-dot { width: 74px; height: 74px; border-radius: 50%; background: var(--orange); margin: 0 auto 12px; }
  .brand-name {
    font-family: "Montserrat", sans-serif; font-weight: 700; font-size: 19px;
    line-height: 22px; color: var(--navy); text-transform: uppercase; letter-spacing: 0.3px;
  }
  .divider { position: absolute; left: 341px; top: 96px; width: 1.5px; height: 74px; background: var(--orange); }
  .contact {
    position: absolute; left: 362px; top: 92px;
    font-family: "Montserrat", sans-serif; font-size: 13.5px; color: var(--ink);
    list-style: none; line-height: 19px;
  }
  .contact li { display: flex; align-items: center; gap: 6px; }
  .contact svg { width: 11px; height: 11px; fill: var(--orange); flex: none; }
  .contact .license { margin-top: 7px; padding-left: 0; }
  .rule-accent { position: absolute; left: 10px; top: 231px; width: 167px; height: 4px; background: var(--orange); }
  .rule-line { position: absolute; left: 177px; top: 233px; right: 0; height: 1.5px; background: var(--navy); }
  .letter { position: absolute; left: 38px; top: 289px; width: 675px; font-size: 15.5px; line-height: 17.5px; }
  .letter p { margin-bottom: 19px; }
  .letter .date { margin-bottom: 19px; }
  .letter .recipient { margin-bottom: 17px; }
  .letter .salutation { font-weight: 700; font-size: 19px; line-height: 22px; margin: 0 0 17px; }
  .letter .body { text-align: justify; margin-bottom: 16px; }
  .letter .closing { margin-top: 38px; }
  .signature {
    position: absolute; left: 38px; top: 888px;
    font-family: "Italianno", cursive; font-size: 42px; color: var(--ink);
  }
  .swoosh { position: absolute; left: 0; top: 0; width: 750px; height: 1060px; }
</style>
</head>
<body>
  <main class="letterhead">
    <div class="brand">
      <div class="brand-dot"></div>
      <div class="brand-name">Copper Ridge<br>Inquiries</div>
    </div>

    <div class="divider"></div>
    <ul class="contact">
      <li><svg viewBox="0 0 12 12"><path d="M6 0a4 4 0 0 0-4 4c0 3 4 8 4 8s4-5 4-8a4 4 0 0 0-4-4zm0 5.6a1.6 1.6 0 1 1 0-3.2 1.6 1.6 0 0 1 0 3.2z"/></svg>FORT HARLAN, TX</li>
      <li><svg viewBox="0 0 12 12"><path d="M1 4c0-2 2-3 5-3s5 1 5 3l-2.5 1V3.5h-5V5zM2 6h8l1 5H1z"/></svg>512.555.0142</li>
      <li><svg viewBox="0 0 12 12"><path d="M1 3h10v7H1zM1.5 3.5 6 7l4.5-3.5" stroke="#efefef" stroke-width="0.8"/></svg>MARA@COPPERRIDGEINQUIRIES.COM</li>
      <li class="license">LICENSE NO. 01694213</li>
    </ul>

    <div class="rule-accent"></div>
    <div class="rule-line"></div>

    <section class="letter">
      <p class="date">January-03-2020</p>
      <p class="recipient">Mr, John Doe<br>President</p>
      <p class="recipient">Ashford Legal Group<br>123 Street Name, Suite# 10<br>City, State, 120023</p>
      <h2 class="salutation">Dear Mr, John</h2>
      <p class="body">Lorem ipsum dolor sit amet, consectetur adipiscing elit, sed do eiusmod tempor incididunt ut labore et dolore magna aliqua. Ut enim ad minim veniam, quis nostrud exercitation ullamco laboris nisi ut aliquip ex ea commodo consequat. Duis aute irure dolor in reprehenderit in voluptate velit esse cillum dolore eu fugiat nulla pariatur.</p>
      <p class="body">Lorem ipsum dolor sit amet, consectetur adipiscing elit, sed do eiusmod tempor incididunt ut labore et dolore magna aliqua. Ut enim ad minim veniam, quis nostrud exercitation ullamco laboris nisi ut aliquip ex ea commodo consequat. Duis aute irure dolor in reprehenderit in voluptate velit esse cillum dolore eu fugiat nulla pariatur.</p>
      <p class="body">Lorem ipsum dolor sit amet, consectetur adipiscing elit, sed do eiusmod tempor incididunt ut labore et dolore magna aliqua. Ut enim ad minim veniam, quis nostrud exercitation ullamco laboris nisi ut aliquip ex ea commodo consequat.</p>
      <p class="body">Excepteur sint occaecat cupidatat non proident, sunt in culpa qui officia deserunt mollit anim id est laborum. re et dolore magnam aliquam quaerat voluptatem.</p>
      <p class="closing">Regards</p>
    </section>

    <div class="signature">Daniel Reyes</div>

    <svg class="swoosh" viewBox="0 0 750 1060" aria-hidden="true">
      <path d="M0 998 Q520 1000 750 878 L750 886 Q520 1018 0 1014 Z" fill="var(--navy)"/>
      <path d="M0 1030 Q540 1028 750 898 L750 1060 L0 1060 Z" fill="var(--orange)"/>
    </svg>
  </main>
</body>
</html>
```